Website for courses for men for making money, health, fitness

I require a website which is going to be a mix of a crypto currency website and website aimed at providing men with money making, health, relationship advice courses and content

The name isn't decided yet so for now please call it something like

KESTREL YARD

A platform dedicated to making men wealthy, physically strong, mentally tough & successful with women

In the top right, I need it to show how many points they have, they must buy points in order to use them to claim the courses.

WHAT WE DO

Kestrel yard is a platform where you can learn everything you need about business, making money, crypto currency, fitness, health, mental toughness and resilience and how to be successful with women all in one place

HOW WILL THIS WORK & WHY SHOULD I BUY POINTS?

xxxxxxxxxxxxxxxxxxxxxxxx
xxxxxxxxxxxxxxxxxxxxxxx
xxxxxxxxxxxxxxxxxxxxx

AFFILIATE SCHEME

EARN UP TO $125 DOLLARS PER PERSON WHO SIGNS UP THROUGH YOUR LINK

START EARNING NOW - button
______________________________________________________

BUY POINTS
(A maximum of only $250 worth of points can be purchased per person until the platform goes fully live)

ROAD MAP & THE MODEL

2023

Q1 - PRE BUY IN FOR POINTS

Q2 - FULL WEBSITE LAUNCH

Q3 - APP LAUNCH

Q4 - IN APP ADVERT LAUNCH

It must have a very slick and sharp eye catching look, and be designed to convert people into purchasing points

some ideas of the feel of the website -

https://brivaloo.io/
https://nestorly.style/
https://plumwick.trelvanta.com/

```html
<!DOCTYPE html>
<html lang="en">
<head>
<meta charset="utf-8">
<title>Kestrel Yard</title>
<link href="https://fonts.googleapis.com/css2?family=Ubuntu:wght@400;500;700&display=swap" rel="stylesheet">
<style>
:root{
  --purple-deep:#22195e;
  --purple:#33287a;
  --purple-mid:#3c2f88;
  --lavender:#f2f0fa;
  --lavender-ring:#bdb5de;
  --orange:#f0a01a;
  --orange-deep:#ee8a0c;
  --text:#333;
  --footer:#232323;
  --white:#fff;
}
*{margin:0;padding:0;box-sizing:border-box}
html,body{width:1200px;height:2415px;overflow:hidden;background:var(--white)}
body{font-family:"Ubuntu",sans-serif;color:var(--text)}
.page{position:relative;width:1200px;height:2415px;overflow:hidden}
.abs{position:absolute}

/* hero */
.hero{left:0;top:0;width:1200px;height:640px;
  background:
    radial-gradient(ellipse 160px 300px at 0 420px, rgba(240,150,40,.75), transparent 80%),
    radial-gradient(ellipse 120px 220px at 1200px 120px, rgba(240,150,40,.6), transparent 80%),
    radial-gradient(ellipse 520px 380px at 470px 300px, #3e2f8a, transparent 80%),
    var(--purple-deep);}
.hero-curve{left:0;top:530px}
.brand{left:111px;top:38px;font-size:25px;font-weight:500;color:var(--white);letter-spacing:.2px}
.nav{left:497px;top:41px;display:flex;gap:20px;font-size:16px;color:var(--white)}
.nav .active{font-weight:700}
.points{left:1017px;top:41px;font-size:16px;color:var(--orange);display:flex;align-items:center;gap:7px}
.hero-title{left:111px;top:178px;width:620px;font-size:34px;font-weight:500;line-height:49px;color:var(--white)}
.hero-title .accent{color:var(--orange)}
.btn{display:flex;align-items:center;justify-content:center;border:2px solid var(--white);border-radius:6px;color:var(--white);font-size:17px;font-weight:500}
.btn-buy{left:112px;top:346px;width:129px;height:52px}
.hero-note{left:111px;top:422px;width:450px;font-size:12px;line-height:22px;color:#e6e3f3;letter-spacing:-.2px}
.hero-photo{left:703px;top:75px;width:356px;height:492px;border-radius:160px 160px 40px 40px;
  background:linear-gradient(180deg,#6b4a3a 0%,#c79a80 22%,#9bb8d8 40%,#7f9fc6 100%);opacity:.9}

/* headings */
.h2{font-size:41px;font-weight:700;color:var(--purple);line-height:49px}
.ul{background:linear-gradient(var(--orange),var(--orange)) no-repeat left bottom/100% 5px;padding-left:4px;margin-left:-4px}

.what-title{left:0;width:1200px;top:627px;text-align:center}
.what-text{left:205px;top:695px;width:790px;text-align:center;font-size:17.5px;line-height:28.5px}
.deco{color:#c9c9cf}

/* how */
.how-band{left:0;top:790px;width:1200px;height:572px;
  background:radial-gradient(ellipse 220px 260px at 1200px 1350px, rgba(240,170,60,.55), transparent 80%) , var(--lavender)}
.how-top{left:0;top:790px}
.how-ring{left:89px;top:909px;width:404px;height:404px;border-radius:50%;background:var(--lavender-ring);border:2px solid var(--purple)}
.how-ring-gold{left:100px;top:910px;width:396px;height:396px;border-radius:50%;border:1.5px solid var(--orange)}
.how-photo{left:110px;top:911px;width:372px;height:372px;border-radius:50%;
  background:linear-gradient(160deg,#9fb7cf 0%,#7d8ea2 40%,#6b5a4e 70%,#3f4a5c 100%)}
.how-title{left:576px;top:965px;width:560px}
.how-text{left:576px;top:1087px;width:514px;font-size:17.5px;line-height:28.3px;text-align:justify}

/* affiliate */
.aff{left:0;top:1373px;width:1200px;height:258px;
  background:radial-gradient(ellipse 560px 240px at 450px 150px, #3e2f88, transparent 85%), var(--purple-deep)}
.aff-title{left:111px;top:1455px;font-size:43px;font-weight:700;color:var(--orange)}
.aff-title .ul{background-image:linear-gradient(var(--white),var(--white))}
.aff-text{left:111px;top:1521px;font-size:21px;color:var(--white)}
.btn-earn{left:902px;top:1477px;width:186px;height:52px}

/* roadmap */
.road-title{left:0;width:1200px;top:1706px;text-align:center;line-height:53px}
.q{width:116px;height:116px;border-radius:50%;background:var(--white);display:flex;align-items:center;justify-content:center;font-size:33px;font-weight:500}
.q-navy{border:12px solid var(--purple-deep);color:var(--orange);box-shadow:0 4px 12px rgba(34,25,94,.35)}
.q-gold{border:12px solid var(--orange);color:var(--purple);box-shadow:0 4px 12px rgba(240,140,20,.4)}
.q-label{width:200px;text-align:center;font-size:17px;line-height:26px;color:#333;letter-spacing:.2px}

/* footer */
.footer{left:0;top:2160px;width:1200px;height:255px}
.foot-brand{left:0;width:1200px;top:2258px;text-align:center;font-size:25px;font-weight:500;color:var(--white)}
.foot-nav{left:0;width:1200px;top:2313px;display:flex;justify-content:center;gap:40px;font-size:16.5px;color:var(--white)}
.foot-copy{left:0;width:1200px;top:2361px;text-align:center;font-size:16px;color:var(--white)}
</style>
</head>
<body>
<div class="page">

  <!-- hero -->
  <section class="abs hero"></section>
  <svg class="abs hero-curve" width="1200" height="112" viewBox="0 0 1200 112"><path d="M0 87 Q600 -70 1200 87 L1200 112 L0 112 Z" fill="var(--white)"/></svg>
  <div class="abs hero-photo" role="img" aria-label="Smiling man in a denim shirt with arms crossed"></div>
  <div class="abs brand">KESTREL YARD</div>
  <nav class="abs nav"><span class="active">Home</span><span>About</span><span>What we do</span><span>Courses</span><span>Recent Blog</span><span>Contact</span></nav>
  <div class="abs points"><svg width="16" height="16" viewBox="0 0 24 24"><path d="M12 2l3 6.5 7 .8-5.2 4.8 1.5 7L12 17.6 5.7 21.1l1.5-7L2 9.3l7-.8z" fill="var(--orange)"/></svg>559 pt</div>
  <h1 class="abs hero-title">A platform dedicated to making men <span class="accent">wealthy, physically strong, mentally tough &amp; successful with women</span></h1>
  <a class="abs btn btn-buy">Buy Points</a>
  <p class="abs hero-note">(A maximum of only $250 worth of points can be purchased per person until the platform goes fully live)</p>

  <!-- what we do -->
  <h2 class="abs h2 what-title">What <span class="ul">we do</span></h2>
  <p class="abs what-text">Kestrel yard is a platform where you can learn everything you need about business, making money, crypto currency, fitness, health, mental toughness and resilience and how to be successful with women all in one place</p>
  <svg class="abs deco" style="left:736px;top:583px" width="32" height="28" viewBox="0 0 32 28" fill="none" stroke="currentColor" stroke-width="1.5"><path d="M16 26 L3 13 A7 7 0 0 1 16 5 A7 7 0 0 1 29 13 Z"/><path d="M4 14 H11 L13 10 L16 18 L19 12 H28"/></svg>
  <svg class="abs deco" style="left:143px;top:785px" width="32" height="28" viewBox="0 0 32 28" fill="none" stroke="currentColor" stroke-width="1.5"><path d="M16 26 L3 13 A7 7 0 0 1 16 5 A7 7 0 0 1 29 13 Z"/><path d="M4 14 H11 L13 10 L16 18 L19 12 H28"/></svg>
  <svg class="abs deco" style="left:1106px;top:607px" width="36" height="28" viewBox="0 0 36 28" fill="none" stroke="currentColor" stroke-width="1.5"><rect x="6" y="4" width="5" height="20" rx="2"/><rect x="25" y="4" width="5" height="20" rx="2"/><path d="M11 14 H25 M2 10 V18 M34 10 V18"/></svg>

  <!-- how -->
  <div class="abs how-band"></div>
  <svg class="abs how-top" width="1200" height="72" viewBox="0 0 1200 72"><path d="M0 0 H1200 V16 Q600 104 0 16 Z" fill="var(--white)"/></svg>
  <div class="abs how-ring"></div>
  <div class="abs how-ring-gold"></div>
  <div class="abs how-photo" role="img" aria-label="Young man with coffee and tablet outdoors in the city"></div>
  <h2 class="abs h2 how-title"><span class="ul">How</span> will this work &amp;<br><span class="ul">Why</span> should I buy points?</h2>
  <p class="abs how-text">Lorem ipsum dolor sit amet, consectetur adipiscing elit, sed do eiusmod tempor incididunt ut labore et dolore magna aliqua. Ut enim ad minim veniam, quis nostrud exercitation ullamco laboris nisi ut aliquip ex ea commodo consequat. Duis aute irure dolor in reprehenderit in voluptate velit esse cillum dolore eu fugiat nulla pariatur. Excepteur sint occaecat cupidatat non proident, sunt in culpa qui officia deserunt mollit anim id est laborum.</p>

  <!-- affiliate -->
  <section class="abs aff"></section>
  <h2 class="abs aff-title">Affiliate <span class="ul">Scheme</span></h2>
  <p class="abs aff-text">Earn up to $125 dollars per person who signs up through your link</p>
  <a class="abs btn btn-earn">Start earning now</a>

  <!-- roadmap -->
  <h2 class="abs h2 road-title">Road map &amp; the model<br><span class="ul">2023</span></h2>
  <svg class="abs" style="left:0;top:1860px" width="1200" height="160" viewBox="0 1860 1200 160" fill="none" stroke="var(--purple-deep)" stroke-width="3" stroke-dasharray="10 9">
    <path d="M245 1940 Q320 1935 380 1970"/>
    <path d="M500 1968 Q600 1910 632 1990"/>
    <path d="M742 1990 Q780 1880 830 1890 Q880 1895 965 1970"/>
    <g stroke-dasharray="none" fill="var(--purple-deep)" stroke="none">
      <path d="M302 1937 l18 9 -18 9 5 -9z"/>
      <path d="M544 1926 l18 5 -16 11 2 -9z"/>
      <path d="M812 1882 l18 5 -17 10 3 -8z"/>
    </g>
  </svg>
  <div class="abs q q-navy" style="left:124px;top:1878px">Q1</div>
  <div class="abs q q-gold" style="left:381px;top:1928px">Q2</div>
  <div class="abs q q-navy" style="left:629px;top:1962px">Q3</div>
  <div class="abs q q-gold" style="left:970px;top:1931px">Q4</div>
  <div class="abs q-label" style="left:82px;top:2013px">PRE BUY IN FOR<br>POINTS</div>
  <div class="abs q-label" style="left:339px;top:1862px">FULL WEBSITE<br>LAUNCH</div>
  <div class="abs q-label" style="left:587px;top:2098px">APP LAUNCH</div>
  <div class="abs q-label" style="left:928px;top:1865px">IN APP ADVERT<br>LAUNCH</div>

  <!-- footer -->
  <svg class="abs footer" width="1200" height="255" viewBox="0 0 1200 255"><path d="M0 1 Q600 105 1200 1 V255 H0 Z" fill="var(--footer)"/></svg>
  <div class="abs foot-brand">KESTREL YARD</div>
  <nav class="abs foot-nav"><span>Home</span><span>About</span><span>What we do</span><span>Courses</span><span>Recent Blog</span><span>Contact</span></nav>
  <p class="abs foot-copy">2022 Kestrel Yard. All Rights Reserved.</p>
</div>
</body>
</html>
```